Create a proposal + product powerpoint

Please see the powerpoint for the slides. There are about 20 slides to be created. Rest of them are for reference and show the design that I like.

I would like to move fast on this, since I need to present it next week (in the week of April 21st).

Please download the current content from here:
https://www.parcelbrook.net/fetch/qRtVmXzLwPkNbYcD

Please make at least 4 slides with the specific content so I can assess your design style.

Target Market(s)

Business Audience and very senior technical audience
Decision Makers

Industry/Entity Type

Product

Colors
e34297
a64599

Requirements
Must have
• Should be very clean, crisp.

I like to use Icons as shown in the powerpoint.... Please see the appendix of the slide deck that shows the various icons. Most of them just have plain text, and I would like to organize so that it does not look like some is just reading text.

I would like to focus on the design aspects so that the audience is clear on how the solution works.

Every page should some graphic element based on the slides shown in the appendix.

```html
<!DOCTYPE html>
<html lang="en">
<head>
<meta charset="utf-8">
<title>Processes</title>
<link rel="stylesheet" href="https://fonts.googleapis.com/css2?family=Roboto+Condensed:wght@400;500&display=swap">
<style>
  :root {
    --brand-purple: #9c1a9c;
    --ring-fill: #a9289d;
    --footer-dark: #991f5c;
    --footer-light: #a64599;
    --accent-pink: #e34297;
    --rule-grey: #d9d9d9;
    --logo-grey: #8a8a8a;
    --white: #ffffff;
  }
  html, body {
    margin: 0;
    padding: 0;
    width: 1200px;
    height: 900px;
    overflow: hidden;
    background: var(--white);
  }
  .slide {
    position: relative;
    width: 1200px;
    height: 900px;
    overflow: hidden;
    background: var(--white);
    font-family: "Roboto Condensed", "Arial Narrow", sans-serif;
  }
  .backdrop-glow {
    position: absolute;
    left: -200px;
    top: 250px;
    width: 700px;
    height: 650px;
    background: radial-gradient(ellipse at 20% 60%, rgba(214, 150, 222, 0.35), rgba(255, 255, 255, 0) 65%);
  }
  .backdrop-pattern {
    position: absolute;
    left: 880px;
    top: 95px;
    width: 320px;
    height: 745px;
    background: linear-gradient(100deg, rgba(255, 255, 255, 0) 0%, rgba(226, 170, 232, 0.55) 40%, rgba(204, 110, 214, 0.8) 100%);
    clip-path: polygon(8% 0, 100% 0, 100% 100%, 12% 100%, 0 50%);
  }
  .slide-title {
    position: absolute;
    left: 39px;
    top: 18px;
    margin: 0;
    font-size: 45px;
    font-weight: 500;
    color: var(--brand-purple);
    letter-spacing: -0.5px;
  }
  .header-rule {
    position: absolute;
    left: 42px;
    top: 89px;
    width: 1151px;
    height: 2px;
    background: var(--rule-grey);
  }
  .logo-box {
    position: absolute;
    left: 1035px;
    top: 12px;
    width: 150px;
    height: 68px;
    border: 2px solid #ececec;
    border-radius: 8px;
    box-shadow: 0 1px 4px rgba(0, 0, 0, 0.12);
    background: var(--white);
    display: flex;
    align-items: center;
    justify-content: center;
    font-size: 28px;
    color: var(--logo-grey);
    letter-spacing: 1px;
    box-sizing: border-box;
  }
  .process-cycle {
    position: absolute;
    left: 295px;
    top: 197px;
    width: 580px;
    height: 580px;
  }
  .cycle-label {
    fill: var(--white);
    font-family: "Roboto Condensed", "Arial Narrow", sans-serif;
    font-size: 30px;
    text-anchor: middle;
    dominant-baseline: central;
  }
  .footer-band {
    position: absolute;
    top: 840px;
    height: 60px;
    display: flex;
    align-items: center;
    color: var(--white);
    font-size: 24px;
    letter-spacing: 0.5px;
  }
  .footer-page {
    left: 0;
    width: 938px;
    background: var(--footer-dark);
    clip-path: polygon(0 0, 906px 0, 938px 100%, 0 100%);
    padding-left: 14px;
    box-sizing: border-box;
  }
  .footer-copyright {
    left: 916px;
    width: 284px;
    background: var(--footer-light);
    clip-path: polygon(0 0, 100% 0, 100% 100%, 34px 100%);
    justify-content: flex-end;
    padding-right: 15px;
    box-sizing: border-box;
  }
</style>
</head>
<body>
<main class="slide">
  <div class="backdrop-glow"></div>
  <div class="backdrop-pattern" role="img" aria-label="Decorative pink and violet triangle pattern"></div>

  <h1 class="slide-title">Processes</h1>
  <div class="header-rule"></div>
  <div class="logo-box">LOGO HERE</div>

  <svg class="process-cycle" viewBox="-290 -290 580 580" aria-label="Process cycle: Manage, Develop, Compare, Deploy, Approve, Audit, Monitor">
    <circle class="cycle-ring" cx="0" cy="0" r="213" fill="none" stroke="var(--ring-fill)" stroke-width="114"/>
    <g class="cycle-dividers" fill="none" stroke-linejoin="miter">
      <g transform="rotate(-86)">
        <polyline points="150,0 212,20 278,0" stroke="rgba(255,255,255,0.45)" stroke-width="12"/>
        <polyline points="150,0 212,20 278,0" stroke="#fff" stroke-width="5"/>
      </g>
      <g transform="rotate(-34.6)">
        <polyline points="150,0 212,20 278,0" stroke="rgba(255,255,255,0.45)" stroke-width="12"/>
        <polyline points="150,0 212,20 278,0" stroke="#fff" stroke-width="5"/>
      </g>
      <g transform="rotate(16.9)">
        <polyline points="150,0 212,20 278,0" stroke="rgba(255,255,255,0.45)" stroke-width="12"/>
        <polyline points="150,0 212,20 278,0" stroke="#fff" stroke-width="5"/>
      </g>
      <g transform="rotate(68.3)">
        <polyline points="150,0 212,20 278,0" stroke="rgba(255,255,255,0.45)" stroke-width="12"/>
        <polyline points="150,0 212,20 278,0" stroke="#fff" stroke-width="5"/>
      </g>
      <g transform="rotate(119.7)">
        <polyline points="150,0 212,20 278,0" stroke="rgba(255,255,255,0.45)" stroke-width="12"/>
        <polyline points="150,0 212,20 278,0" stroke="#fff" stroke-width="5"/>
      </g>
      <g transform="rotate(171.1)">
        <polyline points="150,0 212,20 278,0" stroke="rgba(255,255,255,0.45)" stroke-width="12"/>
        <polyline points="150,0 212,20 278,0" stroke="#fff" stroke-width="5"/>
      </g>
      <g transform="rotate(222.6)">
        <polyline points="150,0 212,20 278,0" stroke="rgba(255,255,255,0.45)" stroke-width="12"/>
        <polyline points="150,0 212,20 278,0" stroke="#fff" stroke-width="5"/>
      </g>
    </g>
    <text class="cycle-label" x="-80" y="-200">Manage</text>
    <text class="cycle-label" x="106" y="-187">Develop</text>
    <text class="cycle-label" x="210" y="-33">Compare</text>
    <text class="cycle-label" x="158" y="146">Deploy</text>
    <text class="cycle-label" x="-15" y="213">Approve</text>
    <text class="cycle-label" x="-177" y="122">Audit</text>
    <text class="cycle-label" x="-204" y="-63">Monitor</text>
  </svg>

  <footer>
    <div class="footer-band footer-page">Page : 01</div>
    <div class="footer-band footer-copyright">Copyright text here</div>
  </footer>
</main>
</body>
</html>
```